Modern Business Card

Modern professional business card with more than just logo and demographic info. Something memorable.

We are a trendy/modern chiropractic group with an emphasis on neurology, hence the minimalist-type brain logo. We want to convey that modern and technical aspect with professionalism and the elite nature of our practice environment.

```html
<!DOCTYPE html>
<html lang="en">
<head>
<meta charset="utf-8">
<title>Meridian Chiropractic – Business Card</title>
<link rel="stylesheet" href="https://fonts.googleapis.com/css2?family=Lora:wght@400&family=Rajdhani:wght@600&display=swap">
<style>
  :root {
    --page-bg: #f1efec;
    --card-bg: #e7e3dd;
    --card-edge: #d6d1ca;
    --brand-blue: #3f679f;
    --ink-dark: #232323;
    --ink-body: #3b3936;
  }
  * { margin: 0; padding: 0; box-sizing: border-box; }
  html, body {
    width: 1200px;
    height: 1054px;
    overflow: hidden;
    background: var(--page-bg);
  }
  .card {
    position: absolute;
    left: 100px;
    top: 224px;
    width: 1000px;
    height: 605px;
    background: var(--card-bg);
    border: 1px solid var(--card-edge);
    border-radius: 4px;
    box-shadow: 0 8px 28px rgba(0,0,0,0.08);
  }
  .brand-disc {
    position: absolute;
    left: 90px;
    top: 170px;
    width: 260px;
    height: 260px;
    border-radius: 50%;
    background: var(--brand-blue);
  }
  .wordmark {
    position: absolute;
    left: 535px;
    top: 62px;
    font-family: "Lora", serif;
    font-weight: 400;
    color: var(--ink-dark);
    text-transform: uppercase;
    line-height: 1.05;
  }
  .wordmark .line-1 { display: block; font-size: 54px; letter-spacing: 1px; }
  .wordmark .line-2 { display: block; font-size: 30px; letter-spacing: 1px; }
  .person-name {
    position: absolute;
    left: 535px;
    top: 206px;
    font-family: "Rajdhani", sans-serif;
    font-weight: 600;
    font-size: 40px;
    color: var(--brand-blue);
  }
  .person-title {
    position: absolute;
    left: 535px;
    top: 264px;
    font-family: "Lora", serif;
    font-size: 23px;
    color: var(--ink-body);
  }
  .contact-list {
    position: absolute;
    left: 535px;
    top: 344px;
    list-style: none;
    font-family: "Lora", serif;
    font-size: 22px;
    color: var(--ink-body);
  }
  .contact-list li {
    display: flex;
    align-items: center;
    height: 37px;
  }
  .contact-list svg {
    width: 22px;
    height: 22px;
    margin-right: 22px;
    fill: var(--ink-body);
    flex-shrink: 0;
  }
  .address {
    position: absolute;
    left: 535px;
    top: 462px;
    font-family: "Lora", serif;
    font-style: normal;
    font-size: 22px;
    line-height: 37px;
    color: var(--ink-body);
  }
</style>
</head>
<body>
  <section class="card">
    <div class="brand-disc"></div>

    <h1 class="wordmark">
      <span class="line-1">Meridian</span>
      <span class="line-2">Chiropractic</span>
    </h1>

    <p class="person-name">Alex Rowan Hart</p>
    <p class="person-title">Managing Director</p>

    <ul class="contact-list">
      <li>
        <svg viewBox="0 0 24 24" aria-hidden="true"><path d="M3 9c0-3 4-5 9-5s9 2 9 5v2h-5V9H8v2H3z M6 12h12l2 8H4z M12 14a2.5 2.5 0 1 0 0 5a2.5 2.5 0 0 0 0-5z"/></svg>
        555-214-0187
      </li>
      <li>
        <svg viewBox="0 0 24 24" aria-hidden="true"><path d="M2 5h20v14H2z M4 7v.5l8 6 8-6V7z" fill-rule="evenodd"/></svg>
        alex@meridianchiropractic.com
      </li>
      <li>
        <svg viewBox="0 0 24 24" aria-hidden="true"><path d="M12 2a10 10 0 1 0 0 20a10 10 0 0 0 0-20zm0 2c1 1.3 1.8 3.2 2 5h-4c.2-1.8 1-3.7 2-5zm-3.2.7A13 13 0 0 0 7.9 9H4.6a8 8 0 0 1 4.2-4.3zm6.4 0A8 8 0 0 1 19.4 9h-3.3a13 13 0 0 0-.9-4.3zM4.1 11h3.7v2H4.1a8 8 0 0 1 0-2zm5.7 0h4.4v2H9.8zm6.4 0h3.7a8 8 0 0 1 0 2h-3.7zM4.6 15h3.3c.2 1.5.5 3 .9 4.3A8 8 0 0 1 4.6 15zm5.4 0h4c-.2 1.8-1 3.7-2 5-1-1.3-1.8-3.2-2-5zm6.1 0h3.3a8 8 0 0 1-4.2 4.3c.4-1.3.7-2.8.9-4.3z"/></svg>
        www.meridianchiropractic.com
      </li>
    </ul>

    <address class="address">
      418 Linden Ave., Fairview,<br>
      Oak Hollow, US 204817
    </address>
  </section>
</body>
</html>
```